Business Intelligence Application - Reporting Menu and Report Criteria Design

Looking for a fresh, effective and user friendly view for the menu structure and reporting criteria screen format for a business reporting application. Initial format completed, content structure is in place, but we need the 'wow' design.. as its a serious professional report/BI tool it has to fall within certain guidelines for clarity and graphics..but we want it to be slick, friendly, great user experience. There is a large amount of complex content to fit into a small space and we need it to be very inviting, modern and intuitive.. If interested, please review the attachment. We have live screens in operation, but feel these could be improved and looking forward to seeing what great creative suggestions could be made. Please review work done to date in the attached.. We are not looking for a total re-design of everything, all the basic business content/structure is there.. but tell us what we could do to improve this in terms of graphic design... particularly the criteria screens.. thanks!
Updates

Reason: Need a few more days to review designs - thanks for all submissions so far, we will make a selection shortly.

Target Market(s)

Business analysts, hotel operations teams, finance analysts hospitality industry

Industry/Entity Type

Hospitality

Coding

Coded - Design and coding required

Number of Pages Required

4 page

Font styles to use
Sans Serif
Other font styles liked:
• Candara, please see example in deck

Colors
3276b5
3176b5
0255a3
85acd3
33a6d7
cee9f5
85cae6

Requirements
Must have
• sharp clear, logical menu structure, (currently it has 'clicks to sub-menus, we need hover over, slide to sub-menus..) colour, styling.. and most focus on revision of criteria.. right now is somewhat heavy, cumbersome.. keep colour and friendly intuitive process steps.. its heavy analytical stuff.. best of luck!
Should not have
• No grey fonts on white or grey screens! many business apps are not readable or sharp.. or fonts are too small.. colourless, so please avoid that.. see our deck - sharp dark (navy) or black fonts on white, or light shading..

```html
<!DOCTYPE html>
<html lang="en">
<head>
<meta charset="utf-8">
<title>Harborline Hotels &amp; Suites – Rooms Perfomance Criteria</title>
<link rel="stylesheet" href="https://fonts.googleapis.com/css2?family=Open+Sans:wght@400;600;700&display=swap">
<style>
  :root {
    --navy-900: #041838;
    --navy-800: #0b2344;
    --navy-700: #1b2e4b;
    --accent: #33a6d7;
    --accent-text: #2aa3d6;
    --cyan: #1ec8d8;
    --ink: #1c2a3a;
    --ink-soft: #5b6573;
    --muted: #a7adb5;
    --line: #e3e7ec;
    --page: #e4eaf0;
    --band: #f5f8fa;
    --white: #ffffff;
    --nav-text: #b7c0cc;
  }
  * { box-sizing: border-box; margin: 0; padding: 0; }
  html, body { width: 1200px; height: 1041px; overflow: hidden; background: var(--page); }
  body { font-family: "Open Sans", Arial, sans-serif; color: var(--ink); }
  .stage { position: absolute; left: 0; top: 0; width: 1153px; height: 1000px; transform: scale(1.0408); transform-origin: 0 0; background: var(--page); overflow: hidden; }
  .abs { position: absolute; }

  /* top bar */
  .topbar { left: 0; top: 0; width: 1153px; height: 79px; background: var(--white); box-shadow: 0 1px 6px rgba(0,0,0,.08); z-index: 5; }
  .brand-mark { left: 26px; top: 20px; width: 40px; height: 40px; border-radius: 50%; background: var(--cyan); }
  .brand-name { left: 84px; top: 28px; font-size: 18px; font-weight: 400; color: var(--ink); white-space: nowrap; }
  .topbar-divider { top: 0; width: 1px; height: 79px; background: var(--line); }
  .topbar-icon { top: 30px; }
  .avatar { left: 801px; top: 17px; width: 45px; height: 45px; border-radius: 50%; background: radial-gradient(circle at 50% 40%, #c9b9a8, #3a4250); border: 2px solid #e6e9ed; }
  .user-greet { left: 861px; top: 23px; font-size: 12.5px; color: var(--ink); }
  .user-date { left: 861px; top: 42px; font-size: 10.5px; color: var(--muted); }

  /* content band */
  .subheader { left: 226px; top: 79px; width: 927px; height: 126px; background: var(--band); }
  .breadcrumb { right: 23px; top: 124px; font-size: 11px; color: var(--muted); white-space: nowrap; }
  .breadcrumb .current { color: var(--accent-text); }
  .report-tab { top: 160px; font-size: 13.5px; color: var(--ink-soft); white-space: nowrap; }

  .view-btn { top: 237px; height: 39px; width: 127px; background: var(--white); border-radius: 3px 3px 0 0; font-size: 12px; color: var(--ink-soft); display: flex; align-items: center; justify-content: center; }

  .criteria { left: 240px; top: 276px; width: 889px; height: 699px; background: var(--white); }
  .criteria-bar { left: 240px; width: 889px; height: 37px; background: var(--accent); color: var(--white); font-size: 11.5px; font-weight: 600; letter-spacing: .3px; display: flex; align-items: center; padding-left: 24px; }
  .bar-action { position: absolute; right: 22px; top: 9px; font-size: 15px; font-weight: 400; }

  .field-label { font-size: 11.5px; color: var(--ink-soft); }
  .field { height: 30px; border: 1px solid var(--line); background: var(--white); border-radius: 2px; font-size: 11px; color: var(--muted); display: flex; align-items: center; padding-left: 14px; }
  .field svg { position: absolute; right: 14px; top: 11px; }

  /* navigation */
  .nav { left: 0; top: 79px; width: 226px; height: 921px; background: var(--navy-900); z-index: 4; }
  .nav-head { left: 0; top: 0; width: 226px; height: 38px; background: var(--navy-800); font-size: 11.5px; letter-spacing: .8px; color: var(--nav-text); padding: 12px 0 0 23px; }
  .nav-item { left: 0; width: 226px; height: 44px; border-bottom: 1px solid #12284a; font-size: 11.5px; letter-spacing: 1px; color: var(--nav-text); font-weight: 400; }
  .nav-item .label { position: absolute; left: 50px; top: 14px; }
  .nav-item .ico { position: absolute; left: 23px; top: 14px; }
  .nav-item .chev { position: absolute; left: 194px; top: 18px; }
  .nav-item.is-open { color: var(--white); font-weight: 600; }
  .nav-sub { left: 51px; font-size: 11.5px; color: #c9d1db; }
  .nav-sub.is-active { color: var(--accent-text); }
  .nav-rail { background: #2a3d5a; width: 1px; }
  .nav-foot { left: 23px; top: 868px; font-size: 11.5px; color: var(--white); line-height: 17px; }
  .nav-foot .hl { color: var(--cyan); }
  .nav-foot small { font-size: 10px; color: var(--nav-text); display: block; }

  .flyout { left: 226px; top: 79px; width: 226px; height: 921px; background: var(--navy-700); z-index: 4; }
  .flyout-head { left: 0; top: 0; width: 226px; height: 38px; background: var(--navy-900); font-size: 12px; color: var(--white); padding: 12px 0 0 23px; }
  .flyout-item { left: 50px; font-size: 11.5px; color: #c9d1db; }
  .flyout-item.is-active { color: var(--accent-text); }
</style>
</head>
<body>
<div class="stage">

  <!-- top bar -->
  <header class="topbar abs">
    <div class="brand-mark abs"></div>
    <div class="brand-name abs">Harborline Hotels &amp; Suites</div>
    <div class="topbar-divider abs" style="left:617px"></div>
    <div class="topbar-divider abs" style="left:697px"></div>
    <div class="topbar-divider abs" style="left:777px"></div>
    <div class="topbar-divider abs" style="left:1073px"></div>
    <svg class="topbar-icon abs" style="left:649px" width="16" height="16" viewBox="0 0 16 16"><circle cx="9.5" cy="6.5" r="5" fill="none" stroke="#b9c0c8" stroke-width="1.4"/><line x1="6" y1="10" x2="1.5" y2="14.5" stroke="#b9c0c8" stroke-width="1.6"/></svg>
    <svg class="topbar-icon abs" style="left:730px" width="14" height="17" viewBox="0 0 14 17"><path d="M7 1a5.5 5.5 0 0 0-3 10.1V13h6v-1.9A5.5 5.5 0 0 0 7 1z" fill="#b9c0c8"/><rect x="4.5" y="14" width="5" height="2" rx="1" fill="#b9c0c8"/></svg>
    <div class="avatar abs" role="img" aria-label="User profile photo"></div>
    <div class="user-greet abs">Welcome Alan Merrow</div>
    <div class="user-date abs">Oct 03, 2017</div>
    <svg class="abs" style="left:1041px;top:37px" width="9" height="6" viewBox="0 0 9 6"><path d="M1 1l3.5 3.5L8 1" fill="none" stroke="#b9c0c8" stroke-width="1.2"/></svg>
    <svg class="abs" style="left:1106px;top:30px" width="17" height="17" viewBox="0 0 24 24"><path fill="#33a6d7" d="M19.4 13a7.5 7.5 0 0 0 0-2l2.1-1.6-2-3.5-2.5 1a7.6 7.6 0 0 0-1.7-1l-.4-2.6h-4l-.4 2.6a7.6 7.6 0 0 0-1.7 1l-2.5-1-2 3.5L4.6 11a7.5 7.5 0 0 0 0 2l-2.1 1.6 2 3.5 2.5-1a7.6 7.6 0 0 0 1.7 1l.4 2.6h4l.4-2.6a7.6 7.6 0 0 0 1.7-1l2.5 1 2-3.5zM12 15.5a3.5 3.5 0 1 1 0-7 3.5 3.5 0 0 1 0 7z"/></svg>
  </header>

  <!-- page band -->
  <div class="subheader abs"></div>
  <div class="breadcrumb abs">Management &nbsp;/&nbsp; Consolidations &nbsp;/&nbsp; <span class="current">Rooms Perfomance</span></div>
  <div class="report-tab abs" style="left:420px">Demand &amp; Risk</div>
  <div class="report-tab abs" style="left:575px">Inventory Analysis</div>
  <div class="report-tab abs" style="left:728px">Place Holder</div>

  <div class="view-btn abs" style="left:380px">Criteria</div>
  <div class="view-btn abs" style="left:511px">Edit View</div>
  <div class="view-btn abs" style="left:642px">Saved View</div>
  <div class="view-btn abs" style="left:773px">Export</div>

  <!-- criteria panel -->
  <section class="criteria abs"></section>
  <div class="criteria-bar abs" style="top:276px">PROPERTIES &amp; REGIONS<span class="bar-action">×</span></div>

  <div class="field-label abs" style="left:701px;top:334px">My Group</div>
  <div class="field abs" style="left:701px;top:356px;width:404px"><svg width="8" height="5" viewBox="0 0 8 5"><path d="M1 1l3 3 3-3" fill="none" stroke="#b9c0c8"/></svg></div>
  <div class="field abs" style="left:264px;top:356px;width:413px"><svg width="8" height="5" viewBox="0 0 8 5"><path d="M1 1l3 3 3-3" fill="none" stroke="#b9c0c8"/></svg></div>
  <div class="field-label abs" style="left:701px;top:396px">Property Search</div>
  <div class="field abs" style="left:701px;top:418px;width:404px"><svg width="8" height="5" viewBox="0 0 8 5"><path d="M1 1l3 3 3-3" fill="none" stroke="#b9c0c8"/></svg></div>
  <div class="field abs" style="left:264px;top:418px;width:413px"><svg width="8" height="5" viewBox="0 0 8 5"><path d="M1 1l3 3 3-3" fill="none" stroke="#b9c0c8"/></svg></div>
  <div class="field-label abs" style="left:701px;top:458px">Property ID</div>
  <div class="field abs" style="left:701px;top:480px;width:404px"><svg width="8" height="5" viewBox="0 0 8 5"><path d="M1 1l3 3 3-3" fill="none" stroke="#b9c0c8"/></svg></div>
  <div class="field abs" style="left:264px;top:480px;width:413px"><svg width="8" height="5" viewBox="0 0 8 5"><path d="M1 1l3 3 3-3" fill="none" stroke="#b9c0c8"/></svg></div>
  <div class="field-label abs" style="left:701px;top:519px">Country Search</div>
  <div class="field abs" style="left:701px;top:541px;width:404px"><svg width="8" height="5" viewBox="0 0 8 5"><path d="M1 1l3 3 3-3" fill="none" stroke="#b9c0c8"/></svg></div>
  <div class="field abs" style="left:264px;top:541px;width:413px"><svg width="8" height="5" viewBox="0 0 8 5"><path d="M1 1l3 3 3-3" fill="none" stroke="#b9c0c8"/></svg></div>

  <div class="criteria-bar abs" style="top:595px">PROPERTY DETAILS<span class="bar-action">×</span></div>

  <div class="field-label abs" style="left:701px;top:654px">Opening Date</div>
  <div class="field abs" style="left:701px;top:676px;width:196px"><svg width="11" height="10" viewBox="0 0 11 10"><rect x=".5" y="1.5" width="10" height="8" fill="none" stroke="#b9c0c8"/><rect x=".5" y="1.5" width="10" height="2.5" fill="#b9c0c8"/></svg></div>
  <div class="field abs" style="left:910px;top:676px;width:195px"><svg width="11" height="10" viewBox="0 0 11 10"><rect x=".5" y="1.5" width="10" height="8" fill="none" stroke="#b9c0c8"/><rect x=".5" y="1.5" width="10" height="2.5" fill="#b9c0c8"/></svg></div>
  <div class="field abs" style="left:264px;top:676px;width:413px"><svg width="8" height="5" viewBox="0 0 8 5"><path d="M1 1l3 3 3-3" fill="none" stroke="#b9c0c8"/></svg></div>
  <div class="field-label abs" style="left:701px;top:715px">Room Capacity</div>
  <div class="field abs" style="left:701px;top:737px;width:196px">From: 00</div>
  <div class="field abs" style="left:910px;top:737px;width:195px">To: 5000</div>
  <div class="field abs" style="left:264px;top:737px;width:413px"><svg width="8" height="5" viewBox="0 0 8 5"><path d="M1 1l3 3 3-3" fill="none" stroke="#b9c0c8"/></svg></div>
  <div class="field-label abs" style="left:701px;top:776px">PMS System</div>
  <div class="field abs" style="left:701px;top:799px;width:404px"><svg width="8" height="5" viewBox="0 0 8 5"><path d="M1 1l3 3 3-3" fill="none" stroke="#b9c0c8"/></svg></div>
  <div class="field abs" style="left:264px;top:799px;width:413px"><svg width="8" height="5" viewBox="0 0 8 5"><path d="M1 1l3 3 3-3" fill="none" stroke="#b9c0c8"/></svg></div>
  <div class="field-label abs" style="left:701px;top:839px">Finance System</div>
  <div class="field abs" style="left:701px;top:861px;width:404px"><svg width="8" height="5" viewBox="0 0 8 5"><path d="M1 1l3 3 3-3" fill="none" stroke="#b9c0c8"/></svg></div>
  <div class="field abs" style="left:264px;top:861px;width:413px"><svg width="8" height="5" viewBox="0 0 8 5"><path d="M1 1l3 3 3-3" fill="none" stroke="#b9c0c8"/></svg></div>

  <div class="criteria-bar abs" style="top:914px">PERFORMANCE<span class="bar-action">+</span></div>

  <!-- navigation -->
  <nav class="nav abs">
    <div class="nav-head abs">NAVIGATION</div>
    <div class="nav-item abs" style="top:38px">
      <svg class="ico" width="10" height="14" viewBox="0 0 10 14"><circle cx="5" cy="3.5" r="3" fill="#8d97a5"/><path d="M0 14v-4a3 3 0 0 1 3-3h4a3 3 0 0 1 3 3v4z" fill="#8d97a5"/></svg>
      <span class="label">ADMIN</span>
      <svg class="chev" width="8" height="5" viewBox="0 0 8 5"><path d="M1 1l3 3 3-3" fill="none" stroke="#8d97a5" stroke-width="1.2"/></svg>
    </div>
    <div class="nav-item is-open abs" style="top:82px">
      <svg class="ico" width="15" height="13" viewBox="0 0 15 13"><rect x="4.5" y="0" width="6" height="4" fill="#fff"/><rect x="1" y="5.5" width="13" height="1.6" fill="#fff"/><rect x="1" y="7" width="1.6" height="3" fill="#fff"/><rect x="6.7" y="4" width="1.6" height="6" fill="#fff"/><rect x="12.4" y="7" width="1.6" height="3" fill="#fff"/><rect x="0" y="9.5" width="4" height="3.5" fill="#fff"/><rect x="5.5" y="9.5" width="4" height="3.5" fill="#fff"/><rect x="11" y="9.5" width="4" height="3.5" fill="#fff"/></svg>
      <span class="label">MANAGEMENT</span>
      <svg class="chev" width="8" height="5" viewBox="0 0 8 5"><path d="M1 1l3 3 3-3" fill="none" stroke="#8d97a5" stroke-width="1.2"/></svg>
    </div>
    <div class="nav-rail abs" style="left:31px;top:126px;height:165px"></div>
    <div class="nav-sub abs" style="top:146px">Summaries</div>
    <div class="nav-sub is-active abs" style="top:174px">Consolidations</div>
    <div class="nav-sub abs" style="top:202px">Communication</div>
    <div class="nav-sub abs" style="top:230px">Cheat Sheet</div>
    <div class="nav-sub abs" style="top:257px">Programs</div>
    <div class="nav-item abs" style="top:292px;border-top:1px solid #12284a">
      <svg class="ico" width="14" height="14" viewBox="0 0 24 24"><path fill="#8d97a5" d="M19.4 13a7.5 7.5 0 0 0 0-2l2.1-1.6-2-3.5-2.5 1a7.6 7.6 0 0 0-1.7-1l-.4-2.6h-4l-.4 2.6a7.6 7.6 0 0 0-1.7 1l-2.5-1-2 3.5L4.6 11a7.5 7.5 0 0 0 0 2l-2.1 1.6 2 3.5 2.5-1a7.6 7.6 0 0 0 1.7 1l.4 2.6h4l.4-2.6a7.6 7.6 0 0 0 1.7-1l2.5 1 2-3.5zM12 15.5a3.5 3.5 0 1 1 0-7 3.5 3.5 0 0 1 0 7z"/></svg>
      <span class="label">INSIGHT</span>
      <svg class="chev" width="8" height="5" viewBox="0 0 8 5"><path d="M1 1l3 3 3-3" fill="none" stroke="#8d97a5" stroke-width="1.2"/></svg>
    </div>
    <div class="nav-item abs" style="top:336px">
      <svg class="ico" width="13" height="13" viewBox="0 0 13 13"><rect x="0" y="0" width="13" height="8" fill="#8d97a5"/><rect x="5.7" y="8" width="1.6" height="5" fill="#8d97a5"/><rect x="3" y="11.5" width="7" height="1.5" fill="#8d97a5"/></svg>
      <span class="label">PLANNING</span>
      <svg class="chev" width="8" height="5" viewBox="0 0 8 5"><path d="M1 1l3 3 3-3" fill="none" stroke="#8d97a5" stroke-width="1.2"/></svg>
    </div>
    <div class="nav-foot abs">© 2017 Corvex <span class="hl">Insight.</span><small>All right reserved.</small></div>
  </nav>

  <aside class="flyout abs">
    <div class="flyout-head abs">Consolidations</div>
    <div class="nav-rail abs" style="left:31px;top:38px;height:168px"></div>
    <div class="abs" style="left:31px;top:66px;width:8px;height:1px;background:var(--accent)"></div>
    <div class="flyout-item abs" style="top:58px">Company Review</div>
    <div class="flyout-item is-active abs" style="top:86px">Room Perfomance</div>
    <div class="flyout-item abs" style="top:114px">F&amp;B Perfomance</div>
    <div class="flyout-item abs" style="top:142px">Competitive Review</div>
    <div class="flyout-item abs" style="top:169px">Operation</div>
  </aside>

</div>
</body>
</html>
```